Harborlight Amusement Collective (HAC)

We need a business card design for Harborlight Amusement Collective. Modern and sleek looking, with all critical information. Open to single or double sided designs, if double sided info needs to be all on one side. The main Logo is Harborlight Amusement collective and must be on the card. The other three logos are for the brands that fall under the group, they might be good on the back.

Industry/Entity Type

Business

```html
<!DOCTYPE html>
<html lang="en">
<head>
<meta charset="utf-8">
<title>Harborlight Amusement Collective — Business Card</title>
<link href="https://fonts.googleapis.com/css2?family=Fira+Sans+Condensed:wght@500&family=Montserrat:wght@400;600&display=swap" rel="stylesheet">
<style>
  :root {
    --backdrop: #e9e7e3;
    --card: #ffffff;
    --navy: #234b86;
    --blue: #2c5ca6;
    --green: #7c9c2f;
    --ink: #222a33;
    --on-blue: #eef3fb;
  }
  * { margin: 0; padding: 0; box-sizing: border-box; }
  html, body {
    width: 1200px; height: 1054px; overflow: hidden;
    background: var(--backdrop);
  }
  .card {
    position: absolute; left: 100px; top: 224px;
    width: 1000px; height: 605px;
    background: var(--card);
    overflow: hidden;
    box-shadow: 0 10px 30px rgba(0,0,0,0.18);
    font-family: "Montserrat", sans-serif;
  }
  .card__waves { position: absolute; inset: 0; width: 100%; height: 100%; }
  .holder { position: absolute; left: 47px; top: 80px; }
  .holder__name {
    font-family: "Fira Sans Condensed", sans-serif;
    font-weight: 500; font-size: 39px; color: var(--navy); line-height: 1;
  }
  .holder__title {
    margin-top: 12px; font-size: 24px; color: var(--ink); line-height: 1;
  }
  .brand {
    position: absolute; left: 470px; top: 66px; width: 495px;
    text-align: center;
  }
  .brand__mark {
    width: 96px; height: 96px; margin: 0 auto 110px;
    background: var(--navy);
  }
  .brand__name {
    font-weight: 600; font-size: 30px; color: var(--navy);
    letter-spacing: 0.5px; white-space: nowrap; line-height: 1;
  }
  .brand__tag {
    display: flex; align-items: center; gap: 16px; margin-top: 12px;
    font-weight: 600; font-size: 27px; letter-spacing: 7px;
    color: var(--navy); line-height: 1;
  }
  .brand__tag::before, .brand__tag::after {
    content: ""; flex: 1; height: 3px; background: var(--navy);
  }
  .address {
    position: absolute; left: 47px; top: 383px;
    color: var(--on-blue); font-size: 23px; line-height: 33px;
  }
  .contacts {
    position: absolute; left: 47px; top: 466px; list-style: none;
    color: var(--on-blue); font-size: 23px;
  }
  .contacts li { display: flex; align-items: center; gap: 26px; height: 36px; }
  .contacts svg { width: 20px; height: 20px; flex: none; }
</style>
</head>
<body>
  <div class="card">
    <svg class="card__waves" viewBox="0 0 1000 605" preserveAspectRatio="none" aria-hidden="true">
      <path d="M0,312 C240,285 420,345 560,430 C700,515 850,548 1000,520 L1000,605 L0,605 Z" fill="var(--blue)"/>
      <path d="M0,282 C230,255 420,295 585,395 C710,470 830,500 1000,448" fill="none" stroke="var(--green)" stroke-width="14"/>
      <path d="M508,440 C640,500 790,500 920,455 C800,485 650,488 508,440 Z" fill="var(--green)"/>
    </svg>

    <div class="holder">
      <h1 class="holder__name">Marlo Kestrel Vance</h1>
      <p class="holder__title">Managing Director</p>
    </div>

    <div class="brand">
      <div class="brand__mark"></div>
      <p class="brand__name">HARBORLIGHT AMUSEMENT</p>
      <p class="brand__tag">COLLECTIVE</p>
    </div>

    <p class="address">58 Lantern Quay,<br>Bayview, US 204817</p>

    <ul class="contacts">
      <li>
        <svg viewBox="0 0 20 20" fill="var(--on-blue)"><path d="M3 6c0-2 3-3 7-3s7 1 7 3v2h-4V6H7v2H3z"/><rect x="4" y="9" width="12" height="8" rx="1"/></svg>
        555.204.8817
      </li>
      <li>
        <svg viewBox="0 0 20 20" fill="none" stroke="var(--on-blue)" stroke-width="1.6"><rect x="2" y="4" width="16" height="12"/><path d="M2 4l8 7 8-7"/></svg>
        mvance@harborlightac.com
      </li>
      <li>
        <svg viewBox="0 0 20 20" fill="none" stroke="var(--on-blue)" stroke-width="1.4"><circle cx="10" cy="10" r="8"/><ellipse cx="10" cy="10" rx="3.5" ry="8"/><path d="M2 10h16M3.5 6h13M3.5 14h13"/></svg>
        www.harborlightac.com
      </li>
    </ul>
  </div>
</body>
</html>
```